Brimsett Gardening Fresh New Website

We are looking to create a simple fresh website for our landscaping business. The website should appeal to a 'high end' audience. We deal with a lot of Embassies and affluent clients who have extremely large gardens that are meticulously maintained. The site is about communicating our excellent landscaping and customer service skills and encouraging new clients to reach out and engage us to take care of their gardens.

The website is basically going to be our business card, it will have almost no functionality other than two 'contact us' forms, one for smaller clients and one for more detailed projects.

The website will not have a lot of written content and will have to show photos of beautifully landscaped gardens.

The main logo in black will influence the site, however, we are open to all suggestions.

We are expecting to have the following pages:
Home Page
Services
About Us
Contact Us
Showcase (photo gallery of our work)

We need someone who can code it to wordpress and be available for minor changes over a number of days. They will be simple tweaks.

```html
<!DOCTYPE html>
<html lang="en">
<head>
<meta charset="utf-8">
<title>Brimsett Gardening</title>
<link rel="stylesheet" href="https://fonts.googleapis.com/css2?family=Unbounded:wght@700;800&family=Montserrat:wght@400;500;600;700&family=Playfair+Display&display=swap">
<style>
:root{
  --ink:#111111;
  --gold:#d4a12a;
  --gold-light:#f1d46c;
  --gold-grad:linear-gradient(90deg,#b8860f,#e9c55a 55%,#f3d97a);
  --white:#ffffff;
  --text:#333333;
  --muted:#6a6a6a;
}
*{box-sizing:border-box;margin:0;padding:0}
html,body{width:1200px;height:4695px;overflow:hidden}
body{position:relative;background:var(--white);font-family:"Montserrat",sans-serif;color:var(--text)}
.abs{position:absolute}
.display{font-family:"Unbounded",sans-serif;font-weight:800;text-transform:uppercase;letter-spacing:.5px}
.btn{position:absolute;display:flex;align-items:center;justify-content:center;background:var(--gold-grad);color:var(--white);font-weight:700;font-size:10px;letter-spacing:1px;text-transform:uppercase;border-radius:20px;font-family:"Unbounded",sans-serif}
.photo{position:absolute}

/* header */
.topbar{position:absolute;left:0;top:0;width:1200px;height:122px;background:rgba(10,10,10,.9);z-index:3}
.navline{position:absolute;left:0;top:69px;width:1200px;height:1px;background:rgba(255,255,255,.15)}
.brand{position:absolute;display:flex;align-items:center;gap:10px;font-family:"Montserrat",sans-serif;font-weight:600;color:var(--gold);font-size:16px;line-height:1.25;text-transform:uppercase}
.brand .dot{width:12px;height:12px;border-radius:50%;background:var(--gold);flex:none}
.info{position:absolute;top:20px;display:flex;align-items:center;gap:10px;color:var(--white);font-size:10px;font-weight:700;line-height:1.35;text-transform:uppercase}
.info .ico{width:28px;height:28px;border-radius:50%;background:var(--gold-grad);display:flex;align-items:center;justify-content:center}
.nav{position:absolute;top:87px;left:396px;display:flex;gap:46px;font-size:11px;font-weight:700;color:var(--white);text-transform:uppercase;letter-spacing:.5px}
.nav .active{color:var(--gold-light);position:relative}
.nav .active::after{content:"";position:absolute;left:0;right:0;bottom:-18px;height:2px;background:var(--gold)}

/* hero */
.hero-photo{left:0;top:0;width:1200px;height:760px;background:linear-gradient(115deg,#2c4219 0%,#557a2a 25%,#87ab44 42%,#d9732a 58%,#3d5a22 72%,#6e9a35 100%)}
.hero-title{left:70px;top:252px;font-size:44px;line-height:1.03;color:var(--white)}
.contact-card{position:absolute;left:733px;top:321px;width:336px;height:425px;background:var(--ink);border-radius:4px;z-index:4;padding:38px 30px 0}
.contact-card h3{font-family:"Playfair Display",serif;font-weight:400;color:var(--gold);text-align:center;font-size:21px}
.contact-card p{font-family:"Unbounded",sans-serif;font-weight:700;color:var(--white);text-align:center;font-size:12.5px;line-height:1.7;margin-top:10px;text-transform:uppercase}
.field{background:var(--white);border-radius:2px;height:36px;font-size:10px;color:var(--muted);padding:0 15px;display:flex;align-items:center}
.row{display:flex;gap:10px;margin-top:8px}
.row .field{flex:1}
.dots{left:496px;top:655px;display:flex;gap:10px}
.dots i{width:9px;height:9px;border-radius:50%;border:1.5px solid var(--white)}
.dots i:first-child{background:var(--white)}

/* about */
.about-accent{left:117px;top:1164px;width:108px;height:100px;background:var(--gold-grad)}
.about-photo{left:130px;top:841px;width:496px;height:412px;background:linear-gradient(180deg,#7fb4dc 0%,#b9d6e6 28%,#b58a5a 40%,#9c7448 52%,#4e8a2d 60%,#3a7a22 100%)}
.about-title{left:704px;top:862px;font-size:33px;line-height:1.2;color:var(--ink)}
.about-text{left:704px;top:960px;width:372px;font-size:13.5px;line-height:1.62;color:var(--text)}

/* services */
.services{left:0;top:1372px;width:1200px;height:1048px;background:linear-gradient(180deg,#262321 0%,#1f1a16 60%,#2b2219 100%)}
.section-title{position:absolute;left:0;width:1200px;text-align:center;font-size:33px}
.rule{position:absolute;left:565px;width:70px;height:3px;background:var(--gold-grad)}
.svc{position:absolute;width:304px;height:341px;overflow:hidden}
.svc .cap{position:absolute;left:10px;right:10px;bottom:12px;height:80px;background:rgba(17,17,17,.88);text-align:center;color:var(--white);padding-top:24px}
.svc .cap b{display:block;font-family:"Unbounded",sans-serif;font-weight:700;font-size:10.5px;letter-spacing:.5px;text-transform:uppercase}
.svc .cap span{display:block;font-size:9.5px;line-height:1.35;margin-top:6px}

/* works */
.work{position:absolute;width:385px}

/* booking */
.booking{left:0;top:3530px;width:1200px;height:665px;background:linear-gradient(180deg,#3a2a1e 0%,#2a1f16 50%,#1f1812 100%)}
.need{left:127px;top:3716px;font-family:"Unbounded",sans-serif;font-weight:700;font-size:16px;color:var(--gold);text-transform:uppercase}
.book-title{left:127px;top:3750px;font-size:30px;line-height:1.36;color:var(--white)}
.book-text{left:127px;top:3917px;width:300px;font-size:13.5px;line-height:1.5;color:#d6d0c8}
.call{left:140px;top:3993px;display:flex;align-items:center;gap:18px;color:var(--white)}
.call .ico{width:46px;height:46px;border-radius:50%;background:var(--gold-grad);display:flex;align-items:center;justify-content:center}
.call b{font-family:"Unbounded",sans-serif;font-size:19px;display:block;line-height:1.2}
.call span{font-family:"Unbounded",sans-serif;font-weight:700;font-size:16px;text-transform:uppercase}
.vline{left:518px;top:3725px;width:2px;height:380px;background:var(--gold)}
.book-form{left:587px;top:3708px;width:482px}
.book-form .field{height:36px;font-size:11px}
.book-form .row{margin-top:17px;gap:12px}
.book-form .row:first-child{margin-top:0}

/* footer */
.footer{left:0;top:4195px;width:1200px;height:500px;background:var(--ink);color:var(--white)}
.ftitle{font-family:"Unbounded",sans-serif;font-weight:700;font-size:13px;text-transform:uppercase}
.fline{display:flex;align-items:center;gap:12px;font-size:8.5px;font-weight:700;line-height:1.4;text-transform:uppercase;margin-top:14px}
.fline .ico{width:24px;height:24px;border-radius:50%;background:var(--gold-grad);flex:none}
.links{font-size:11px;line-height:20px;margin-top:14px}
.newsletter p{font-size:10.5px;line-height:1.5;margin-top:14px}
.news-input{margin-top:14px;width:277px;height:34px;border:1px solid #666;border-radius:18px;display:flex;align-items:center;justify-content:space-between;padding:0 4px 0 16px;font-size:11px}
.news-input i{width:26px;height:26px;border-radius:50%;background:var(--gold-grad)}
.socials{left:500px;top:4515px;display:flex;gap:8px}
.socials i{width:32px;height:32px;border-radius:50%;border:2px solid var(--gold)}
.legal{left:0;top:4580px;width:1200px;text-align:center;font-size:14px;color:#e4e4e4;word-spacing:2px}
.copy{left:0;top:4633px;width:1200px;text-align:center;font-size:14px;color:#e4e4e4}
.footer-split{left:0;top:4472px;width:1200px;height:1px;background:#2c2c2c}
</style>
</head>
<body>

<!-- Hero -->
<div class="photo hero-photo" role="img" aria-label="Gardener in an orange cap and shirt kneeling to trim a shrub in a green landscaped garden"></div>
<svg class="abs" style="left:0;top:600px" width="1200" height="180" viewBox="0 0 1200 180" aria-hidden="true">
  <defs><linearGradient id="g1" x1="0" x2="1"><stop offset="0" stop-color="#b8860f"/><stop offset="1" stop-color="#f3d97a"/></linearGradient></defs>
  <path d="M0 20 C300 90 700 70 900 70 C1050 65 1150 35 1200 10 L1200 180 L0 180 Z" fill="url(#g1)"/>
  <path d="M0 20 C300 100 700 90 900 82 C1050 78 1150 60 1200 40 L1200 180 L0 180 Z" fill="#ffffff"/>
</svg>

<header class="topbar">
  <div class="brand" style="left:62px;top:38px"><span class="dot"></span>Brimsett<br>Gardening</div>
  <div class="info" style="left:485px"><span class="ico"><svg width="12" height="12" viewBox="0 0 12 12"><circle cx="6" cy="6" r="5" fill="none" stroke="#fff" stroke-width="1.4"/><path d="M6 3v3l2 1.5" stroke="#fff" stroke-width="1.4" fill="none"/></svg></span><div>Open<br>Mon-Sat: 08.00 - 18.00</div></div>
  <div class="info" style="left:722px"><span class="ico"><svg width="12" height="12" viewBox="0 0 24 24"><path d="M6.6 10.8a15 15 0 006.6 6.6l2.2-2.2a1 1 0 011-.25 11 11 0 003.6.6 1 1 0 011 1V20a1 1 0 01-1 1A17 17 0 013 4a1 1 0 011-1h3.5a1 1 0 011 1 11 11 0 00.6 3.6 1 1 0 01-.25 1z" fill="#fff"/></svg></span><div>Call us<br>+1 555 0134 2290</div></div>
  <div class="info" style="left:911px"><span class="ico"><svg width="12" height="12" viewBox="0 0 24 24"><path d="M3 6h18v12H3z" fill="#fff"/><path d="M3 6l9 7 9-7" stroke="#c8961f" stroke-width="2" fill="none"/></svg></span><div>Send an email<br>info@brimsettgardening.com</div></div>
  <div class="navline"></div>
  <nav class="nav"><span class="active">Home</span><span>About us</span><span>Our services</span><span>Showcase</span><span>Contact us</span></nav>
  <div class="btn" style="left:1005px;top:78px;width:129px;height:34px">Get started</div>
</header>

<h1 class="abs display hero-title">Brimsett<br>Gardening<br>&amp; Landscape<br>Services</h1>
<div class="btn" style="left:71px;top:456px;width:142px;height:33px">Learn more</div>
<div class="abs dots"><i></i><i></i><i></i><i></i></div>

<form class="contact-card">
  <h3>Contact Us</h3>
  <p>Book a free professional<br>gardening consultation!</p>
  <div class="row" style="margin-top:18px"><div class="field">First name</div><div class="field">Last name</div></div>
  <div class="row"><div class="field">Email address</div></div>
  <div class="row"><div class="field">Phone</div></div>
  <div class="row"><div class="field" style="height:70px;align-items:flex-start;padding-top:12px">Message</div></div>
  <div class="btn" style="position:relative;margin-top:10px;height:38px;border-radius:3px">Send message</div>
</form>

<!-- About -->
<div class="abs about-accent"></div>
<div class="photo about-photo" role="img" aria-label="Gardener in green overalls holding rake, shears, watering can, plant pot and spade on a lawn by a wooden fence"></div>
<h2 class="abs display about-title">About Brimsett<br>Gardening</h2>
<p class="abs about-text">Sed ut perspiciatis unde omnis iste natus error sit voluptatem accusantium doloremque laudantium, totam rem aperiam, eaque ipsa quae ab illo inventore veritatis et quasi architecto beatae vitae dicta sunt explicabo. Nemo enim ipsam voluptatem quia voluptas sit aspernatur aut odit aut fugit, sed quia consequuntur magni dolores eos qui ratione voluptatem sequi nesciunt. Neque porro quisquam est, qui dolorem ipsum quia dolor sit amet, consectetur, adipisci velit,</p>
<div class="btn" style="left:704px;top:1193px;width:142px;height:34px">Learn more</div>

<!-- Services -->
<section class="abs services" role="img" aria-label="Dark soil background with garden tools and plants along the bottom edge"></section>
<h2 class="display section-title" style="top:1455px;color:var(--white)">Our services</h2>
<div class="rule" style="top:1512px"></div>

<div class="svc" style="left:130px;top:1563px"><div class="photo" style="inset:0;background:linear-gradient(180deg,#3f6a2a 0%,#7fa3b8 30%,#c05a7a 50%,#8a8070 70%,#4f7a2b 100%)" role="img" aria-label="Patio with garden chairs surrounded by flower beds and shrubs"></div><div class="cap"><b>Excepteur sint occaecat</b><span>Sed ut perspiciatis unde omnis<br>iste natus voluptatem</span></div></div>
<div class="svc" style="left:448px;top:1563px"><div class="photo" style="inset:0;background:linear-gradient(180deg,#2f5a22 0%,#dcd6c4 25%,#4f7a2b 45%,#7fc23d 70%,#6db032 100%)" role="img" aria-label="Neat green lawn bordered by hydrangeas and hedges"></div><div class="cap"><b>Excepteur sint occaecat</b><span>Sed ut perspiciatis unde omnis<br>iste natus voluptatem</span></div></div>
<div class="svc" style="left:766px;top:1563px"><div class="photo" style="inset:0;background:linear-gradient(180deg,#c9d2d0 0%,#7a9a4a 35%,#d8a23a 50%,#5a7a3a 70%,#3c5a2a 100%)" role="img" aria-label="Gardener trimming an ornamental topiary tree"></div><div class="cap"><b>Excepteur sint occaecat</b><span>Sed ut perspiciatis unde omnis<br>iste natus voluptatem</span></div></div>
<div class="svc" style="left:130px;top:1917px"><div class="photo" style="inset:0;background:linear-gradient(135deg,#4f7a2b 0%,#8fb64a 35%,#e37b2e 55%,#6a9a32 75%,#3f5f22 100%)" role="img" aria-label="Gardener in an orange cap cutting a hedge with shears"></div><div class="cap"><b>Excepteur sint occaecat</b><span>Sed ut perspiciatis unde omnis<br>iste natus voluptatem</span></div></div>
<div class="svc" style="left:448px;top:1917px"><div class="photo" style="inset:0;background:linear-gradient(180deg,#6a8c45 0%,#d9d2c4 35%,#2f5a2a 55%,#4a3a28 80%,#3a2d20 100%)" role="img" aria-label="Gardener planting a seedling in soil"></div><div class="cap"><b>Excepteur sint occaecat</b><span>Sed ut perspiciatis unde omnis<br>iste natus voluptatem</span></div></div>
<div class="svc" style="left:766px;top:1917px"><div class="photo" style="inset:0;background:linear-gradient(135deg,#b7b9b4 0%,#6f8fb0 35%,#d95a9a 50%,#a03a3a 65%,#4a5a34 100%)" role="img" aria-label="Gloved hands holding a potted flowering plant"></div><div class="cap"><b>Excepteur sint occaecat</b><span>Sed ut perspiciatis unde omnis<br>iste natus voluptatem</span></div></div>
<div class="btn" style="left:489px;top:2296px;width:222px;height:35px">View more our services</div>

<!-- Recent works -->
<h2 class="display section-title" style="top:2500px;color:var(--ink)">Our recent works</h2>
<div class="rule" style="top:2556px"></div>
<div class="photo work" style="left:11px;top:2606px;height:341px;background:linear-gradient(160deg,#6b9a3a 0%,#d23a5a 30%,#e4572e 50%,#3e2c1f 75%,#2e2018 100%)" role="img" aria-label="Gloved hands planting white flowers with a trowel"></div>
<div class="photo work" style="left:11px;top:2956px;height:418px;background:linear-gradient(160deg,#8ab04c 0%,#e37b2e 35%,#4d6f2c 60%,#a83a3a 85%,#5a2a22 100%)" role="img" aria-label="Gardener in an orange cap tending a flower bed"></div>
<div class="photo work" style="left:407px;top:2606px;height:418px;background:linear-gradient(160deg,#3f6a28 0%,#6f9a3a 40%,#d8dcd6 60%,#d9562a 75%,#2e4a1e 100%)" role="img" aria-label="Hedge trimmer cutting a green hedge"></div>
<div class="photo work" style="left:407px;top:3033px;height:341px;background:linear-gradient(160deg,#2f5a5a 0%,#3a4a4a 30%,#4a3527 55%,#d8d0c0 75%,#2e2218 100%)" role="img" aria-label="Gloved hands planting a seedling beside a watering can"></div>
<div class="photo work" style="left:803px;top:2606px;height:341px;background:linear-gradient(160deg,#9ab2c4 0%,#5a6f8a 30%,#8fc23d 55%,#5a4030 80%,#3d2e22 100%)" role="img" aria-label="Gardener holding a flowering plant with roots above soil"></div>
<div class="photo work" style="left:803px;top:2956px;height:418px;background:linear-gradient(180deg,#a9cbe6 0%,#3f6a28 30%,#4f7a2b 55%,#7a4a2a 68%,#7fb83f 80%,#6aa832 100%)" role="img" aria-label="Garden table and chairs on a lawn surrounded by trees"></div>
<div class="btn" style="left:445px;top:3422px;width:308px;height:38px">View more our latest projects</div>

<!-- Booking -->
<section class="abs booking" role="img" aria-label="Dark soil with terracotta pots, seedling trays and a metal bucket"></section>
<svg class="abs" style="left:0;top:3529px" width="1200" height="110" viewBox="0 0 1200 110" aria-hidden="true">
  <defs><linearGradient id="g2" x1="0" x2="1"><stop offset="0" stop-color="#b8860f"/><stop offset="1" stop-color="#f3d97a"/></linearGradient></defs>
  <path d="M0 0 H1200 V52 C800 50 350 70 0 94 Z" fill="url(#g2)"/>
  <path d="M0 0 H1200 V18 C800 20 350 55 0 90 Z" fill="#ffffff"/>
</svg>
<div class="abs need">Need any help?</div>
<h2 class="abs display book-title">Book a free<br>professional<br>gardening<br>consultation!</h2>
<p class="abs book-text">Lorem ipsum dolor sit amet, consectetur adipiscing elit, sed do eiusmod tempor incididunt ut labore et dolore</p>
<div class="abs call"><span class="ico"><svg width="20" height="20" viewBox="0 0 24 24"><path d="M6.6 10.8a15 15 0 006.6 6.6l2.2-2.2a1 1 0 011-.25 11 11 0 003.6.6 1 1 0 011 1V20a1 1 0 01-1 1A17 17 0 013 4a1 1 0 011-1h3.5a1 1 0 011 1 11 11 0 00.6 3.6 1 1 0 01-.25 1z" fill="#fff"/></svg></span><div><span>Call us</span><b>+1 555 0134 2290</b></div></div>
<div class="abs vline"></div>
<form class="abs book-form">
  <div class="row"><div class="field">First name</div><div class="field">Last name</div></div>
  <div class="row"><div class="field">Email address</div></div>
  <div class="row"><div class="field">Phone</div><div class="field">Subject</div></div>
  <div class="row"><div class="field" style="justify-content:space-between">Choose Services<svg width="10" height="6" viewBox="0 0 10 6"><path d="M1 1l4 4 4-4" stroke="#333" stroke-width="1.5" fill="none"/></svg></div></div>
  <div class="row"><div class="field" style="height:196px;align-items:flex-start;padding-top:14px">Message</div></div>
  <div class="btn" style="position:relative;margin-top:20px;width:164px;height:34px">Send message</div>
</form>

<!-- Footer -->
<footer class="abs footer">
  <div class="brand" style="left:128px;top:112px;font-size:20px"><span class="dot"></span>Brimsett<br>Gardening</div>
  <div class="abs" style="left:360px;top:62px">
    <div class="ftitle">Contact us</div>
    <div class="fline"><span class="ico"></span><div>Call us<br>+1 555 0134 2290</div></div>
    <div class="fline"><span class="ico"></span><div>Open<br>Mon-Sat: 08.00 - 18.00</div></div>
    <div class="fline"><span class="ico"></span><div>Send an email<br>info@brimsettgardening.com</div></div>
  </div>
  <div class="abs" style="left:619px;top:62px">
    <div class="ftitle">Quick links</div>
    <div class="links">Home<br>About Us<br>Services<br>Showcase<br>Contact Us</div>
  </div>
  <div class="abs newsletter" style="left:792px;top:62px;width:285px">
    <div class="ftitle">Sign-up to our newsletter</div>
    <p>Lorem ipsum dolor sit amet, consectetur adipiscing elit, sed do eiusmod tempor incididunt ut labore et dolore magna aliqua. Quis ipsum</p>
    <div class="news-input">Email Address<i></i></div>
  </div>
</footer>
<div class="abs footer-split"></div>
<div class="abs socials"><i></i><i></i><i></i><i></i><i></i></div>
<div class="abs legal">Terms Of Use &nbsp;&nbsp; | &nbsp;&nbsp; Privacy Policy &nbsp;&nbsp; | &nbsp;&nbsp; Cookies Policy &nbsp;&nbsp; | &nbsp;&nbsp; Cookie Settings</div>
<div class="abs copy">© 2024 Brimsett Gardening. All rights reserved.</div>

</body>
</html>
```